Industry / Entity Type

Financial consultancy / advisers

Current site is: http://www.brightmoor-counsel.com

Looking for a complete overhaul of this site, we are after a clean modern look. Will require the ability to easily add, update and remove content, hence the WordPress design.
Example:
Add case studies
Industry documentation (downloadable brochures / flyers and such)

What we like from our current site is the colour the fonts and the logo (the city of London) we would like to have other city outlines (NYC and Tokyo, Hong Kong, Singapore).

The site will be used by our potential clients to get in contact and re-view the case studies, if possible would like to have a client login area where they can download our documents like NDA’s etc and T&C’s.

Task Outline

Create a Web Design (Coded - Design and coding required)
Designer must provide full implementation/coding depending on the platform chosen by the client (i.e. WordPress theme, HTML/CSS, bootstrap etc.)

Task Description

I need a full website built that must work on desktop and mobile. I can provide the London city skyline and the font file, which we have used. Some stock industrial photos will be required.

Requirements:

*Splash page
*What We Do
*How We do it
*Who Are We? To have the same information and links as the current site
*Why use us?
*Clients: To have the same information and links as the current site
*Partners: To have the same information and links as the current site
*Contact:

Target Market(s)

Financial institutions trading Equities, Futures, Options, Forex and Fixed Income.
Regulators, Exchanges, ECN’s
Buy side firms and Sell side firms

Industry/Entity Type

Financial

Coding

Coded - Design and coding required

Number of Pages Required

5+ page

Font styles to use
Sans Serif

Colors
f04a50

Requirements
Must have
• Splash page
• What We Do
• How We do it
• Who Are We? To have the same information and links as the current site
• Why use us?
• Clients: To have the same information and links as the current site
• Partners: To have the same information and links as the current site
• Contact:

```html
<!DOCTYPE html>
<html lang="en">
<head>
<meta charset="utf-8">
<title>Brightmoor Counsel</title>
<link rel="stylesheet" href="https://fonts.googleapis.com/css2?family=Maven+Pro:wght@400;500;600&family=Michroma&display=swap">
<style>
:root{
  --brand:#f04a50;
  --ink:#222428;
  --text:#6b6d70;
  --muted:#8a8c8f;
  --panel:#f4f4f4;
  --line:#d9d9d9;
  --white:#ffffff;
}
*{box-sizing:border-box;margin:0;padding:0}
html,body{width:1200px;height:2258px;overflow:hidden}
body{position:relative;background:var(--white);font-family:"Maven Pro",Arial,sans-serif;color:var(--text)}
.abs{position:absolute}
.display{font-family:"Michroma","Maven Pro",sans-serif;font-weight:400;color:var(--ink)}

/* hero */
.hero{left:0;top:0;width:1200px;height:520px;overflow:hidden}
.hero-photo{position:absolute;inset:0;background:linear-gradient(180deg,#6f8397 0%,#a9b9c6 40%,#b9c4cc 62%,#9aa7b0 100%)}
.hero-boat{position:absolute;left:470px;top:260px;width:240px;height:200px;background:radial-gradient(ellipse at center,rgba(150,60,50,.55),rgba(150,60,50,0) 70%)}
.hero-top{position:absolute;left:0;top:0;width:1200px;height:100px;background:linear-gradient(180deg,rgba(30,40,55,.55),rgba(30,40,55,0));border-bottom:1px solid rgba(255,255,255,.35)}
.brand-mark{left:93px;top:36px;display:flex;align-items:center;gap:10px;color:var(--white);font-family:"Maven Pro",sans-serif;font-weight:500;font-size:17px;letter-spacing:2px;text-transform:uppercase}
.brand-mark .dot{width:14px;height:14px;border-radius:50%;background:var(--white)}
.nav{left:410px;top:40px;display:flex;gap:0;font-size:15px;color:var(--white)}
.nav a{color:var(--white);text-decoration:none;margin-right:23px}
.nav a.active{color:var(--brand)}
.nav svg{margin-top:3px}
.hero-title{left:0;top:200px;width:1200px;text-align:center;font-family:"Michroma",sans-serif;color:var(--white);font-size:36px;letter-spacing:1px;text-shadow:0 2px 4px rgba(0,0,0,.25)}
.hero-sub{left:0;top:266px;width:1200px;text-align:center;color:var(--white);font-size:19px;line-height:33px;letter-spacing:.5px;text-shadow:0 1px 3px rgba(0,0,0,.3)}
.btn-hero{left:486px;top:355px;width:226px;height:45px;border-radius:23px;background:var(--brand);border:2px solid var(--white);color:var(--white);font-size:16px;font-weight:500;text-align:center;line-height:41px;letter-spacing:.5px}
.dots{left:566px;top:480px;display:flex;gap:6px}
.dots span{width:13px;height:13px;border-radius:50%;border:2px solid var(--white)}
.dots span.on{background:var(--white)}

/* welcome */
.welcome-title{left:0;top:604px;width:1200px;text-align:center;font-size:27px}
.welcome-text{left:230px;top:656px;width:740px;text-align:center;font-size:12px;line-height:26px}
.service{width:260px;text-align:center}
.service svg{display:block;margin:0 auto}
.service h3{margin-top:55px;font-size:20px;font-weight:500;color:var(--ink);letter-spacing:.5px}
.service p{margin-top:10px;font-size:12.5px;line-height:21px;color:var(--muted)}

/* how */
.how{left:0;top:1047px;width:1200px;height:412px;background:var(--panel);border-top:1px solid #e4e4e4;border-bottom:1px solid #e4e4e4}
.how-photo{position:absolute;left:0;top:0;width:622px;height:412px;clip-path:polygon(0 0,622px 0,517px 412px,0 412px);background:radial-gradient(circle at 260px 170px,#d9b56a 0%,#6f5b3c 22%,#3a4049 50%,#2e3440 100%)}
.how-title{left:664px;top:1105px;font-size:26px}
.how-text{left:664px;top:1160px;width:440px;font-size:12.5px;line-height:25px}
.how-text p+p{margin-top:24px}
.btn-line{height:31px;border:1px solid #9a9a9a;border-radius:16px;color:var(--brand);font-size:12.5px;font-weight:600;text-align:center;line-height:29px;letter-spacing:.5px}

/* why */
.why-title{left:99px;top:1543px;font-size:26px}
.why-list{left:99px;top:1600px;list-style:none;font-size:13px}
.why-list li{height:37px;display:flex;align-items:center;gap:12px}
.laptop{left:629px;top:1536px;width:523px;height:309px}
.laptop-screen{position:absolute;left:53px;top:0;width:417px;height:283px;background:#1b1b1d;border-radius:12px 12px 0 0;padding:14px}
.laptop-screen div{width:100%;height:100%;background:linear-gradient(180deg,#f4f5f9,#e3e6ef)}
.laptop-base{position:absolute;left:0;top:283px;width:523px;height:16px;background:linear-gradient(180deg,#e4e4e4,#a8a8a8);border-radius:0 0 40px 40px}

/* footer */
.footer-rule{left:0;top:1904px;width:1200px;height:4px;background:var(--brand)}
.footer-brand{left:75px;top:2030px;display:flex;align-items:center;gap:10px;color:var(--ink);font-weight:500;font-size:17px;letter-spacing:2px;text-transform:uppercase}
.footer-brand .dot{width:14px;height:14px;border-radius:50%;background:var(--ink)}
.col-title{font-family:"Michroma",sans-serif;color:var(--ink);font-size:16px}
.info-links{list-style:none;font-size:13px;line-height:19.8px;margin-top:14px}
.news-text{font-size:12.5px;line-height:21px;margin-top:16px;width:230px}
.news-input{margin-top:20px;width:253px;border-bottom:1px solid #bdbdbd;font-size:12px;color:#9a9a9a;padding:0 0 10px 14px}
.contact-row{display:flex;gap:16px;font-size:12.5px;line-height:21px}
.contact-row svg{flex:none;margin-top:4px}
.footer-divider{left:99px;top:2182px;width:1003px;height:1px;background:var(--line)}
.copyright{left:99px;top:2215px;font-size:12px}
.social{left:976px;top:2209px;display:flex;gap:9px}
.social span{width:25px;height:25px;border-radius:50%;border:1px solid var(--brand);display:flex;align-items:center;justify-content:center}
.social span i{width:7px;height:7px;border-radius:50%;background:var(--brand)}
</style>
</head>
<body>

<header class="abs hero">
  <div class="hero-photo" role="img" aria-label="City harbour skyline with a red-sailed junk boat on the water"></div>
  <div class="hero-boat"></div>
  <div class="hero-top"></div>
  <div class="abs brand-mark"><span class="dot"></span>Brightmoor Counsel</div>
  <nav class="abs nav">
    <a class="active">Home</a><a>What we do</a><a>How we do it</a><a>Who are we</a><a>Why use us</a><a>Clients</a><a>Partners</a><a>Contact</a>
    <svg width="13" height="13" viewBox="0 0 13 13"><circle cx="5.5" cy="5.5" r="4" fill="none" stroke="#fff" stroke-width="2"/><line x1="8.5" y1="8.5" x2="12" y2="12" stroke="#fff" stroke-width="2"/></svg>
  </nav>
  <h1 class="abs hero-title">BRIGHTMOOR COUNSEL</h1>
  <p class="abs hero-sub">Provide solutions to solve potential issues to get you the correct solution<br>at the correct price point to achieve the desired results</p>
  <div class="abs btn-hero">GET MORE INFO &gt;&gt;</div>
  <div class="abs dots"><span class="on"></span><span></span><span></span><span></span></div>
</header>

<h2 class="abs display welcome-title">Welcome to Brightmoor Counsel</h2>
<p class="abs welcome-text">Since founding Brightmoor Counsel in 2014 we have dedicated ourselves to the provision of services. What differentiates us from other advisers or consultancies is a genuine motivation to see our clients succeed.</p>

<div class="abs service" style="left:73px;top:753px">
  <svg width="110" height="100" viewBox="0 0 110 100">
    <rect x="44" y="2" width="62" height="84" fill="#f04a50"/>
    <g stroke="#fff" stroke-width="4"><line x1="56" y1="20" x2="96" y2="20"/><line x1="56" y1="34" x2="96" y2="34"/><line x1="56" y1="48" x2="96" y2="48"/><line x1="56" y1="62" x2="96" y2="62"/></g>
    <circle cx="24" cy="32" r="12" fill="none" stroke="#f04a50" stroke-width="7" stroke-dasharray="5 3"/>
    <circle cx="28" cy="74" r="16" fill="none" stroke="#f04a50" stroke-width="9" stroke-dasharray="6 3"/>
    <circle cx="28" cy="74" r="7" fill="#fff" stroke="#f04a50" stroke-width="3"/>
  </svg>
  <h3>Data Management</h3>
  <p>At vero eos et accusamus et iustodi<br>dignissimos ducimus qui blan</p>
</div>

<div class="abs service" style="left:338px;top:753px">
  <svg width="110" height="100" viewBox="0 0 110 100">
    <circle cx="55" cy="50" r="42" fill="none" stroke="#f04a50" stroke-width="13" stroke-dasharray="60 5"/>
    <rect x="36" y="56" width="9" height="16" fill="#f04a50"/><rect x="50" y="46" width="9" height="26" fill="#f04a50"/><rect x="64" y="34" width="9" height="38" fill="#f04a50"/>
  </svg>
  <h3>Analytics</h3>
  <p>At vero eos et accusamus et iustodi<br>dignissimos ducimus qui blan</p>
</div>

<div class="abs service" style="left:602px;top:753px">
  <svg width="120" height="100" viewBox="0 0 120 100">
    <ellipse cx="44" cy="52" rx="38" ry="30" fill="#f04a50"/><path d="M14 70 L4 96 L36 78 Z" fill="#f04a50"/>
    <ellipse cx="72" cy="40" rx="42" ry="32" fill="#f04a50" stroke="#fff" stroke-width="4"/><path d="M98 60 L112 88 L82 68 Z" fill="#f04a50"/>
    <circle cx="56" cy="40" r="5" fill="#fff"/><circle cx="72" cy="40" r="5" fill="#fff"/><circle cx="88" cy="40" r="5" fill="#fff"/>
  </svg>
  <h3>Consulting</h3>
  <p>At vero eos et accusamus et iustodi<br>dignissimos ducimus qui blan</p>
</div>

<div class="abs service" style="left:865px;top:753px">
  <svg width="110" height="100" viewBox="0 0 110 100">
    <ellipse cx="55" cy="50" rx="50" ry="22" fill="none" stroke="#f04a50" stroke-width="6" transform="rotate(40 55 50)"/>
    <ellipse cx="55" cy="50" rx="50" ry="22" fill="none" stroke="#f04a50" stroke-width="6" transform="rotate(-40 55 50)"/>
    <circle cx="55" cy="48" r="24" fill="#f04a50" stroke="#fff" stroke-width="3"/>
    <g fill="none" stroke="#fff" stroke-width="2"><ellipse cx="55" cy="48" rx="10" ry="24"/><line x1="31" y1="48" x2="79" y2="48"/><line x1="35" y1="36" x2="75" y2="36"/><line x1="35" y1="60" x2="75" y2="60"/></g>
  </svg>
  <h3>Trading</h3>
  <p>At vero eos et accusamus et iustodi<br>dignissimos ducimus qui blan</p>
</div>

<section class="abs how">
  <div class="how-photo" role="img" aria-label="Glowing light bulb with gears inside against a chalkboard of formulas"></div>
</section>
<h2 class="abs display how-title">How We Do It</h2>
<div class="abs how-text">
  <p>At vero eos et accusamus et iusto odio dignissimos ducimus qui blanditiis prasent ium voluptatum deleniti atque corrupti quo.</p>
  <p>Dolores et quas molestias excepturi sint occaecati cupiditate non provident similiq ue sunt in culpa qui officia deserunt mollitia animi, id est laborum et dolorum fug t harum quidem rerum facilis est et expedita voluptas assumen est, omnis dolorr epellend poribus autem quibusdam et aut officiis.</p>
</div>
<div class="abs btn-line" style="left:664px;top:1363px;width:133px">READ MORE &gt;&gt;</div>

<h2 class="abs display why-title">Why Choose us</h2>
<ul class="abs why-list">
  <li><svg width="15" height="15" viewBox="0 0 15 15"><circle cx="7.5" cy="7.5" r="7.5" fill="#f04a50"/><path d="M4 7.5l2.5 2.5 4.5-5" fill="none" stroke="#fff" stroke-width="2"/></svg>At vero eos et accusamus et iusto odio dignissimos ducimus qui blaniis</li>
  <li><svg width="15" height="15" viewBox="0 0 15 15"><circle cx="7.5" cy="7.5" r="7.5" fill="#f04a50"/><path d="M4 7.5l2.5 2.5 4.5-5" fill="none" stroke="#fff" stroke-width="2"/></svg>Praesentium voluptatum deleniti atque corrupti quos dolores et quas</li>
  <li><svg width="15" height="15" viewBox="0 0 15 15"><circle cx="7.5" cy="7.5" r="7.5" fill="#f04a50"/><path d="M4 7.5l2.5 2.5 4.5-5" fill="none" stroke="#fff" stroke-width="2"/></svg>Excepturi sint occaecati cupiditate non provident, similiqt in culpa qui</li>
  <li><svg width="15" height="15" viewBox="0 0 15 15"><circle cx="7.5" cy="7.5" r="7.5" fill="#f04a50"/><path d="M4 7.5l2.5 2.5 4.5-5" fill="none" stroke="#fff" stroke-width="2"/></svg>Nam libero tempore, cum soluta nobis est eligendi optio</li>
  <li><svg width="15" height="15" viewBox="0 0 15 15"><circle cx="7.5" cy="7.5" r="7.5" fill="#f04a50"/><path d="M4 7.5l2.5 2.5 4.5-5" fill="none" stroke="#fff" stroke-width="2"/></svg>Dit quo minus id quod maxime placeat facere possimus, omnis volup</li>
</ul>
<div class="abs btn-line" style="left:99px;top:1800px;width:143px">READ MORE &gt;&gt;</div>

<div class="abs laptop">
  <div class="laptop-screen"><div role="img" aria-label="Trading platform screenshot showing a candlestick price chart"></div></div>
  <div class="laptop-base"></div>
</div>

<div class="abs footer-rule"></div>
<div class="abs footer-brand"><span class="dot"></span>Brightmoor Counsel</div>

<div class="abs" style="left:399px;top:1964px">
  <h4 class="col-title">Information</h4>
  <ul class="info-links"><li>Home</li><li>What we do</li><li>How we do it</li><li>Who are we</li><li>Why use us</li><li>Clients</li><li>Partners</li><li>Contact</li></ul>
</div>

<div class="abs" style="left:590px;top:1964px">
  <h4 class="col-title">Newsletter Subscription</h4>
  <p class="news-text">Register your Email Address to get Information about us</p>
  <div class="news-input">Email Address</div>
  <div class="btn-line" style="margin-top:22px;width:95px;height:29px;line-height:27px;font-weight:400;font-size:12px">SUBSCRIBE</div>
</div>

<div class="abs" style="left:916px;top:1964px">
  <h4 class="col-title">Contact Us</h4>
  <div class="contact-row" style="margin-top:22px"><svg width="9" height="12" viewBox="0 0 9 12"><path d="M4.5 0a4.5 4.5 0 0 0-4.5 4.5C0 8 4.5 12 4.5 12S9 8 9 4.5A4.5 4.5 0 0 0 4.5 0z" fill="#f04a50"/><circle cx="4.5" cy="4.5" r="1.6" fill="#fff"/></svg><span>Suite 4 Harrow Court,<br>Lindale, Westford,<br>Oxon, OX9 2LT</span></div>
  <div class="contact-row" style="margin-top:20px"><svg width="11" height="11" viewBox="0 0 11 11"><path d="M2 0l2 2.5-1.2 1.5a7 7 0 0 0 4 4L8.5 7 11 9 9.5 11C4 11 0 7 0 1.5z" fill="#f04a50"/></svg><span>+1-555-014-2270</span></div>
  <div class="contact-row" style="margin-top:20px"><svg width="12" height="10" viewBox="0 0 12 10"><rect width="12" height="10" fill="#f04a50"/><path d="M0 0l6 5 6-5" fill="none" stroke="#fff" stroke-width="1.3"/></svg><span>info@brightmoor-counsel.com</span></div>
</div>

<div class="abs footer-divider"></div>
<p class="abs copyright">Copyrights © 2017, Brightmoor Counsel. All rights reserved.</p>
<div class="abs social"><span><i></i></span><span><i></i></span><span><i></i></span><span><i></i></span></div>

</body>
</html>
```